redesign of my existing custom website into Wordpress based website

I need someone to redesign my current website into something more classy, simplistic, modern and on trend. I would like it set up on Wordpress in a way thats easy for me to make my own additions to blogs/price changes and promotion banners. I will also need a page that is password protected so members can login and have access to all my training videos and resources.
website is www.tidewellmamas.com.au

Target Market(s)

new mums

Industry/Entity Type

Fitness

Coding

Coded - Design and coding required

Number of Pages Required

5+ page

Colors
33a6d7

Requirements
Must have
• chic, modern, stylish and simplistic.
• a call to action above the page fold
• mobile friendly conversion
• a pop up message as soon as someone enters my sight offering my free report
• a members page that is password protected containing 3 youtube videos and 6 pdf attachments as resources
• a home page
• a contact us page
• an about us page
• a blog page
• a store page
Nice to have
• some examples of my peers websites that I like:
• www.norapellwick.com
• https://www.9qlr.com
• https://41bytedgarth.com
Should not have
• anything gimmicky

```html
<!DOCTYPE html>
<html lang="en">
<head>
<meta charset="utf-8">
<title>Contact – Tidewell Mamas</title>
<link rel="stylesheet" href="https://fonts.googleapis.com/css2?family=Lato:wght@400;700;900&family=Open+Sans:wght@400;600&display=swap">
<style>
  :root {
    --pink: #e8187f;
    --ink: #2b2b2b;
    --text: #5f5f5f;
    --muted: #6e6e6e;
    --line: #bdbdbd;
    --field: #a9a9a9;
    --white: #ffffff;
  }
  * { box-sizing: border-box; margin: 0; padding: 0; }
  html, body { width: 908px; height: 1200px; overflow: hidden; background: var(--white); }
  body { position: relative; font-family: "Open Sans", Arial, sans-serif; color: var(--text); }

  .site-header { position: absolute; top: 0; left: 0; width: 908px; height: 70px; border-top: 3px solid var(--pink); background: var(--white); }
  .brand { position: absolute; left: 96px; top: 20px; display: flex; align-items: center; gap: 6px; font-family: "Lato", sans-serif; font-weight: 700; font-size: 15px; color: var(--ink); }
  .brand-dot { width: 22px; height: 22px; border: 2px solid var(--ink); border-radius: 50%; }
  .main-nav { position: absolute; top: 26px; left: 278px; display: flex; font-family: "Lato", sans-serif; font-weight: 700; font-size: 11.5px; color: var(--ink); }
  .main-nav span { margin-right: 27.5px; }
  .main-nav .is-current { color: var(--pink); }
  .btn-login { position: absolute; left: 682px; top: 19px; width: 74px; height: 26px; border: 1px solid var(--line); border-radius: 13px; display: flex; align-items: center; justify-content: center; gap: 5px; font-family: "Lato", sans-serif; font-size: 11.5px; font-weight: 700; color: var(--ink); }
  .btn-join { position: absolute; left: 762px; top: 19px; width: 72px; height: 26px; border-radius: 13px; background: var(--pink); color: var(--white); font-family: "Lato", sans-serif; font-size: 11px; font-weight: 700; display: flex; align-items: center; justify-content: center; }

  .hero { position: absolute; top: 70px; left: 0; width: 908px; height: 237px; background: linear-gradient(90deg, #6f6a66 0%, #3d3a3c 35%, #4a4350 60%, #3a3440 100%); display: flex; align-items: center; justify-content: center; }
  .hero-photo { position: absolute; inset: 0; background: linear-gradient(180deg, rgba(30,30,35,0.15) 0%, rgba(70,55,120,0.45) 100%); }
  .hero-title { position: relative; text-align: center; font-family: "Lato", sans-serif; font-weight: 900; font-size: 26px; line-height: 40px; color: var(--white); letter-spacing: -0.3px; text-shadow: 0 2px 3px rgba(0,0,0,0.45); }

  .breadcrumb { position: absolute; left: 74px; top: 330px; font-family: "Lato", sans-serif; font-size: 11.5px; font-weight: 700; color: var(--ink); }
  .breadcrumb .is-current { color: var(--pink); }
  .rule { position: absolute; left: 74px; width: 760px; height: 1px; background: #cfcfcf; }

  .portrait { position: absolute; left: 73px; top: 414px; width: 300px; height: 443px; border: 1px solid #d8d8d8; padding: 3px; box-shadow: 0 0 3px rgba(0,0,0,0.15); background: var(--white); }
  .portrait-fill { width: 100%; height: 100%; background: linear-gradient(160deg, #d9d3ca 0%, #b8c46a 45%, #2a2a2a 75%, #5b4f8f 100%); }

  .contact { position: absolute; left: 406px; top: 410px; width: 428px; }
  .contact h1 { font-family: "Lato", sans-serif; font-weight: 700; font-size: 20.5px; color: var(--ink); }
  .contact-intro { margin-top: 10px; font-size: 12px; line-height: 22px; color: var(--muted); }
  .field-label { position: absolute; left: 2px; font-size: 10.5px; color: var(--muted); }
  .field { position: absolute; left: 1px; width: 426px; height: 27px; border: 1px solid var(--field); background: var(--white); }
  .btn-contact { position: absolute; left: 1px; top: 409px; width: 139px; height: 38px; border-radius: 19px; background: var(--pink); color: var(--white); font-weight: 600; font-size: 12.5px; display: flex; align-items: center; justify-content: center; letter-spacing: 0.3px; }

  .site-footer { position: absolute; top: 914px; left: 0; width: 908px; height: 286px; border-top: 3px solid var(--pink); }
  .footer-brand { position: absolute; left: 74px; top: 82px; display: flex; align-items: center; gap: 8px; font-family: "Lato", sans-serif; font-weight: 700; font-size: 20px; color: var(--ink); }
  .footer-brand .brand-dot { width: 32px; height: 32px; }
  .footer-col { position: absolute; top: 50px; }
  .footer-col h2 { font-weight: 400; font-size: 14px; color: var(--ink); margin-bottom: 8px; }
  .quick-links li { list-style: none; font-size: 9px; line-height: 21.6px; color: var(--muted); }
  .subscribe-text { font-size: 8.5px; line-height: 17.6px; color: var(--muted); width: 210px; }
  .sub-field { width: 210px; height: 23px; border: 1px solid var(--field); font-size: 8.5px; color: var(--muted); padding: 5px 8px; margin-top: 5px; }
  .sub-field:first-of-type { margin-top: 12px; }
  .btn-subscribe { margin-top: 9px; margin-left: 1px; width: 90px; height: 28px; border-radius: 14px; background: var(--pink); color: var(--white); font-weight: 600; font-size: 10px; display: flex; align-items: center; justify-content: center; }
  .social { display: flex; align-items: center; gap: 14px; font-size: 8.5px; color: var(--muted); margin-top: 12px; }
  .social-mark { width: 22px; height: 22px; border-radius: 4px; background: #b5b5b5; }
  .copyright { position: absolute; left: 0; top: 253px; width: 908px; text-align: center; font-size: 9px; color: var(--muted); }
</style>
</head>
<body>
  <header class="site-header">
    <div class="brand"><span class="brand-dot"></span>Tidewell Mamas</div>
    <nav class="main-nav">
      <span>HOME</span><span>PROGRAM</span><span>BLOG</span><span>FAQ</span><span>ABOUT</span><span class="is-current">CONTACT</span>
    </nav>
    <div class="btn-login">
      <svg width="8" height="10" viewBox="0 0 8 10"><rect x="0.5" y="4" width="7" height="6" rx="1" fill="#e8187f"/><path d="M2 4V2.8a2 2 0 0 1 4 0V4" stroke="#e8187f" stroke-width="1.3" fill="none"/></svg>
      LOGIN
    </div>
    <div class="btn-join">JOIN</div>
  </header>

  <section class="hero">
    <div class="hero-photo" role="img" aria-label="Mum holding a plank on an exercise mat in a living room, with a step and hand weights"></div>
    <h2 class="hero-title">AN EXERCISE PROGRAM SPECIALLY DESIGNED<br>FOR MUMS &amp; CREATED BY A MUM</h2>
  </section>

  <div class="breadcrumb">HOME &nbsp;&gt;&gt;&nbsp; <span class="is-current">CONTACT</span></div>
  <div class="rule" style="top:359px"></div>

  <figure class="portrait">
    <div class="portrait-fill" role="img" aria-label="Smiling trainer in a lime tank top sitting on an exercise mat"></div>
  </figure>

  <section class="contact">
    <h1>CONTACT FORM</h1>
    <p class="contact-intro">If you have any questions or would like to send us a message please fill in your details below and we will get back to you shortly.</p>
    <span class="field-label" style="top:95px">Name :</span>
    <div class="field" style="top:120px"></div>
    <span class="field-label" style="top:163px">Email Address :</span>
    <div class="field" style="top:188px"></div>
    <span class="field-label" style="top:228px">Subject:</span>
    <div class="field" style="top:251px"></div>
    <span class="field-label" style="top:293px">Message :</span>
    <div class="field" style="top:316px;height:69px"></div>
    <div class="btn-contact">CONTACT US</div>
  </section>

  <footer class="site-footer">
    <div class="footer-brand"><span class="brand-dot"></span>Tidewell Mamas</div>

    <div class="footer-col" style="left:290px">
      <h2>Quick Links</h2>
      <ul class="quick-links">
        <li>Home</li><li>Program</li><li>Blog</li><li>FAQ</li><li>About</li><li>Contact</li>
      </ul>
    </div>

    <div class="footer-col" style="left:420px">
      <h2>Subscribe</h2>
      <p class="subscribe-text">Register your details below and receive tones of free information on fitness and living a healthy lifestyle</p>
      <div class="sub-field">Name :</div>
      <div class="sub-field">Email :</div>
      <div class="btn-subscribe">SUBSCRIBE</div>
    </div>

    <div class="footer-col" style="left:676px">
      <h2>Stay Connected</h2>
      <div class="social"><span class="social-mark"></span>Circlebook</div>
      <div class="social"><span class="social-mark"></span>Snapgram</div>
    </div>

    <div class="rule" style="top:233px"></div>
    <p class="copyright">Copyrights © 2017, Tidewell Mamas. All rights reserved.</p>
  </footer>
</body>
</html>
```